BrivoNest Learning App for Children with Dyslexia

Project Description:

We are seeking a talented UI/UX designer to create engaging and intuitive designs for Brivonest, an innovative educational app designed to help children learn letters and words through a multisensory learning approach. The app aims to be particularly helpful for children with dyslexia, providing a supportive and interactive learning environment.

Key App Features & Design Requirements:

Account Creation Screen: Design a welcoming and straightforward sign-up page that allows users to register with their email or continue with Quarnix. The design should be clean, focusing on user-friendliness and accessibility, adhering to our terms of service and privacy policy.

Main Screen Design: The main screen should allocate at least 4/6 of its height to the interactive drawing area. It needs to display word prompts in both correct and scrambled orders and include options to "Show all Words," "Play all words," and a search function. The interface should be vibrant, engaging, and easy to navigate for children.

Profile Section: Create a user-friendly profile page that allows users to edit their profile image, name, username, email, links, and bio. The design should be clean and encourage user engagement.

BrivoTally Page: This section will display the user's learning progress, including rankings, a learning curve, and recently learned words. It should visually represent progress in a motivating and understandable way, suitable for a younger audience.

Visual and Auditory Feedback Implementation: Incorporate elements that support visual and auditory feedback, using dyslexia-friendly formats. This includes choosing appropriate colors, fonts, and auditory cues.

Accessibility and Customization Settings: Designs should include settings for adjusting visual contrast, font size, and the word list to accommodate individual preferences and needs.

Feel free to add more interactions and/or pages.

Design preferences:

Color Scheme: Use a bright, inviting color palette that stimulates learning and engagement without overwhelming the users.
Font Selection: Opt for fonts that are readable and accessible, particularly for users with dyslexia.
Icons and Graphics: Design custom icons and graphics that are cohesive with the app's theme and purpose. Illustrations should be simple, relatable, and supportive of the learning process.

Target Market(s)

Educational

Industry/Entity Type

Educational

Colors
0054AA
0677BA
7BADD7
CADEEF
E8F1F8
0094D4
00A9DD
6FCCEA
C7EBF8
E9F6FB

Requirements
Must have
• Educational app, a writing area, scoring and account management
Nice to have
• Statistics, Ranking Page, Settings and some nice visual features

```html
<!DOCTYPE html>
<html lang="en">
<head>
<meta charset="utf-8">
<title>Brivonest – App Screens</title>
<link rel="stylesheet" href="https://fonts.googleapis.com/css2?family=Merriweather:wght@400;700&display=swap">
<style>
:root{
  --navy:#0054AA;
  --blue:#0094D4;
  --sky:#00A9DD;
  --sky-light:#6FCCEA;
  --ice:#E9F6FB;
  --stage:#dedcdf;
  --row:#f3f3f3;
  --ink:#1c1c1c;
  --green:#2fae4e;
  --grass:#8fcf4a;
}
*{box-sizing:border-box;margin:0;padding:0}
html,body{width:1200px;height:788px;overflow:hidden}
body{background:var(--stage);font-family:"Merriweather",serif;color:var(--ink);position:relative}
.screen{position:absolute;top:31px;width:361px;height:697px;overflow:hidden}
.screen--signup{left:28px;background:linear-gradient(180deg,#0ea8e0,#22b6e8 60%,#5fc9ef)}
.screen--main{left:427px;width:340px;background:linear-gradient(180deg,#fff,#f4f8fa);border-radius:26px}
.screen--profile{left:806px;background:linear-gradient(180deg,var(--ice),#fff 30%)}
.abs{position:absolute}

/* sign up */
.brand{top:32px;width:100%;text-align:center;color:#fff;font-size:24px;font-weight:700}
.tagline{top:73px;width:100%;text-align:center;color:#fff;font-size:15px;font-weight:700}
.card{left:32px;top:100px;width:297px;height:358px;background:#fff;border-radius:14px}
.card__title{top:28px;width:100%;text-align:center;font-size:17px;font-weight:700}
.card__sub{top:63px;width:100%;text-align:center;font-size:10.5px}
.field{left:18px;top:84px;width:265px;height:38px;background:#eee;font-size:10px;padding:13px 0 0 17px}
.btn-email{left:18px;top:126px;width:265px;height:39px;background:var(--navy);color:#fff;font-size:12.5px;font-weight:700;text-align:center;line-height:39px}
.divider{left:0;top:178px;width:100%;display:flex;align-items:center;font-size:12px;gap:12px;padding:0 0}
.divider::before,.divider::after{content:"";flex:1;height:1px;background:#ccc}
.btn-provider{left:18px;top:214px;width:265px;height:39px;background:#eee;display:flex;align-items:center;justify-content:center;gap:10px;font-size:10.5px}
.provider-dot{width:16px;height:16px;border-radius:50%;background:var(--blue)}
.terms{left:24px;top:275px;width:250px;display:flex;gap:14px;font-size:9.5px;line-height:15px}
.terms__box{width:10px;height:10px;border:1px solid #bbb;margin-top:2px;flex:none}

/* scenes */
.scene{left:0;bottom:0;width:100%}
.scene__art{position:absolute;left:0;bottom:0;width:100%}
.scene__wave{position:absolute;left:0;top:0;width:100%;height:40px}

/* main */
.menu{left:22px;top:42px}
.main-title{top:37px;width:100%;text-align:center;color:var(--blue);font-size:16.5px;font-weight:700}
.points{right:24px;top:40px;font-size:12.5px;font-weight:700}
.canvas-box{left:18px;top:82px;width:305px;height:206px;border:5px solid var(--sky);background:#fff}
.tools{right:12px;top:12px;display:flex;flex-direction:column;gap:10px}
.tool{width:25px;height:25px;background:#fff;box-shadow:0 1px 3px rgba(0,0,0,.25);display:flex;align-items:center;justify-content:center}
.btn{height:35px;font-size:11.5px;text-align:center;line-height:35px}
.btn--ghost{left:43px;top:315px;width:123px;background:#e8e8e8}
.btn--play{left:174px;top:315px;width:123px;background:var(--sky);color:#fff;font-weight:700}
.word{width:96px;height:30px;background:#fff;box-shadow:0 1px 3px rgba(0,0,0,.2);font-size:12px;text-align:center;line-height:30px}
.btn--results{left:101px;top:469px;width:139px;height:36px;line-height:36px;background:var(--green);color:#fff;font-weight:700;font-size:11.5px}

/* profile */
.back{left:26px;top:20px}
.profile-title{top:22px;width:100%;text-align:center;color:var(--blue);font-size:17px;font-weight:700}
.avatar{left:28px;top:87px;width:84px;height:72px;background:linear-gradient(160deg,#9fb7c9,#6a8aa6 60%,#c9a98c)}
.edit-photo{left:134px;top:114px;font-size:14px;font-weight:700}
.row{left:27px;width:305px;background:var(--row);font-size:11px}
.row__label{position:absolute;left:11px;top:17px}
.row__value{position:absolute;left:122px;top:17px}
.row__chev{position:absolute;right:12px;top:17px}
.links{position:absolute;left:122px;top:16px;display:flex;flex-direction:column;gap:14px}
</style>
</head>
<body>

<section class="screen screen--signup">
  <h1 class="abs brand">Brivonest</h1>
  <p class="abs tagline">Learn letters and words</p>
  <div class="abs card">
    <h2 class="abs card__title">Create an account</h2>
    <p class="abs card__sub">Enter your email to sign up for this app</p>
    <div class="abs field">email@sample.test</div>
    <div class="abs btn-email">SignUp With Email</div>
    <div class="abs divider">or continue with</div>
    <div class="abs btn-provider"><span class="provider-dot"></span>Quarnix</div>
    <div class="abs terms"><span class="terms__box"></span><span>By clicking continue, you agree to our Terms of Service and Privacy Policy</span></div>
  </div>
  <div class="abs scene" style="height:220px">
    <div class="scene__art" role="img" aria-label="Children playing on large colourful letters A, B and C in a meadow" style="top:20px;background:linear-gradient(180deg,#eaf7fd,#f7e3f3 45%,#c9e79b 80%,var(--grass))"></div>
    <svg class="scene__wave" viewBox="0 0 361 40" preserveAspectRatio="none">
      <path d="M0 22 C40 4 70 34 110 18 S180 4 220 20 S300 30 361 10 L361 0 L0 0Z" fill="#22b6e8"/>
      <path d="M0 22 C40 4 70 34 110 18 S180 4 220 20 S300 30 361 10" fill="none" stroke="#fff" stroke-width="5"/>
      <path d="M0 30 C40 12 70 40 110 26 S180 12 220 28 S300 36 361 18" fill="none" stroke="var(--sky)" stroke-width="3"/>
    </svg>
  </div>
</section>

<section class="screen screen--main">
  <svg class="abs menu" width="22" height="18" viewBox="0 0 22 18"><g stroke="#222" stroke-width="2.4" stroke-linecap="round"><line x1="2" y1="2" x2="20" y2="2"/><line x1="2" y1="9" x2="20" y2="9"/><line x1="2" y1="16" x2="20" y2="16"/></g></svg>
  <h1 class="abs main-title">Main Screen</h1>
  <span class="abs points">16 Points</span>
  <div class="abs canvas-box">
    <div class="abs tools">
      <span class="tool"><svg width="16" height="16" viewBox="0 0 16 16"><path d="M3 13 L11 5 L13 7 L5 15 L2 15Z" fill="#f5a623"/></svg></span>
      <span class="tool"><svg width="16" height="16" viewBox="0 0 16 16"><g stroke-width="2"><line x1="3" y1="4" x2="3" y2="14" stroke="#e74c3c"/><line x1="6" y1="3" x2="6" y2="14" stroke="#27ae60"/><line x1="9" y1="4" x2="9" y2="14" stroke="#2980b9"/><line x1="12" y1="3" x2="12" y2="14" stroke="#8e44ad"/></g></svg></span>
      <span class="tool"><svg width="16" height="16" viewBox="0 0 16 16"><circle cx="8" cy="8" r="6" fill="#f0a64a"/><circle cx="6" cy="6" r="1.5" fill="#e74c3c"/><circle cx="10" cy="6" r="1.5" fill="#2980b9"/><circle cx="7" cy="10" r="1.5" fill="#27ae60"/></svg></span>
      <span class="tool"><svg width="16" height="16" viewBox="0 0 16 16"><rect x="3" y="5" width="11" height="6" rx="1" transform="rotate(-40 8 8)" fill="#f06b6b"/></svg></span>
      <span class="tool"><svg width="16" height="16" viewBox="0 0 16 16"><circle cx="6" cy="5" r="2.5" fill="#2d6fd6"/><rect x="2" y="9" width="8" height="5" rx="2" fill="#2d6fd6"/><path d="M10 12 L14 8" stroke="#f5a623" stroke-width="2"/></svg></span>
    </div>
  </div>
  <div class="abs btn btn--ghost">Show all Words</div>
  <div class="abs btn btn--play">Play all words</div>
  <div class="abs word" style="left:18px;top:375px">Word 1</div>
  <div class="abs word" style="left:121px;top:375px">Word 2</div>
  <div class="abs word" style="left:223px;top:375px">Word 3</div>
  <div class="abs word" style="left:18px;top:413px">Word 4</div>
  <div class="abs word" style="left:121px;top:413px">Word 5</div>
  <div class="abs word" style="left:223px;top:413px">Word 6</div>
  <div class="abs btn btn--results">Show Me The Results</div>
  <div class="abs scene" style="height:172px">
    <div class="scene__art" role="img" aria-label="Cheerful children with giant letter blocks A, B and C, books and a globe" style="top:18px;background:linear-gradient(180deg,#dff3fb,#fbe0ea 45%,#d8ecb5 80%,#a9d86a)"></div>
    <svg class="scene__wave" viewBox="0 0 340 40" preserveAspectRatio="none">
      <path d="M0 24 C40 4 80 34 120 18 S200 6 240 22 S300 30 340 14" fill="none" stroke="var(--sky)" stroke-width="4"/>
    </svg>
  </div>
</section>

<section class="screen screen--profile">
  <svg class="abs back" width="20" height="16" viewBox="0 0 20 16"><path d="M18 8 H3 M9 2 L3 8 L9 14" fill="none" stroke="#222" stroke-width="2" stroke-linecap="round" stroke-linejoin="round"/></svg>
  <h1 class="abs profile-title">Profile</h1>
  <div class="abs avatar" role="img" aria-label="Profile photo of the user"></div>
  <p class="abs edit-photo">Edit profile image</p>

  <div class="abs row" style="top:185px;height:42px"><span class="row__label">Name</span><span class="row__value">Marla Voss</span><span class="row__chev">›</span></div>
  <div class="abs row" style="top:236px;height:42px"><span class="row__label">Username</span><span class="row__value">@username</span><span class="row__chev">›</span></div>
  <div class="abs row" style="top:286px;height:42px"><span class="row__label">Email</span><span class="row__value">name@sample.test</span><span class="row__chev">›</span></div>
  <div class="abs row" style="top:336px;height:137px"><span class="row__label">Links</span>
    <div class="links"><span>brightpage.test</span><span>myspot.test</span><span>yourspot.test</span><span>+ Add link</span></div>
  </div>
  <div class="abs row" style="top:482px;height:42px"><span class="row__label">Bio</span><span class="row__value">A description of this user.</span><span class="row__chev">›</span></div>

  <div class="abs scene" style="height:152px">
    <div class="scene__art" role="img" aria-label="Group of happy children jumping on green grass" style="top:16px;background:linear-gradient(180deg,#ffffff,#f3f7fb 55%,#c8e79a 85%,var(--grass))"></div>
    <svg class="scene__wave" viewBox="0 0 361 40" preserveAspectRatio="none">
      <path d="M0 10 C40 26 80 4 120 16 S200 28 240 14 S310 6 361 22" fill="none" stroke="var(--sky)" stroke-width="4"/>
    </svg>
  </div>
</section>

</body>
</html>
```